Dunfield Inc 1 pg brochure for entrepreneurs

We need a one page brochure (2 sided) designed for a finance and strategy consulting company called Dunfield Inc. which does work in Canada and the United States currently. This company works with entrepreneurs, helping them to establish finance operations, evaluate their financial infomation and apply insight from it to business strategies. Essentially we help entrepreneurs grow their business ... we take care of their finance needs and give them sound business advice ... allowing them to focus on their core business and business strategy.

This one page brochure is meant to caputure what services we provide but also positon that we are also entrepreneurs and we understand how entrepreneurs think .... we not only bring technical competence but cultural insight in this regard as well. We understand how nimble and stealth an entrepreneur's business is so we don't gouge them with expensive consulting fees. We don't want to look like a massive corporation ...we want to look professional, smart and reliable. We want to reflect that we are entrepreneural ourselves even in fact that we have a niche offering that is totally targeted to businesses of this nature.

Major emphasis points for the piece are
1) our core values, this could be a side bar or box
2) the credentials of our founder, he is technically competent and an entrepreneur himself (we have his picture to include)
3) our offerings, what we can do for a company, the client quotes provided are a good illustration of what we offer, the relief we provide a client and of what value we provide - make sure you read these, this could also be a side bar or box, some kind of special call out so the service offerings are very clear

The brochure needs to be editable, so in a format that we can work with it for future, if we need to make updates, one that we can use in Microsoft word and convert to a PDF format. It will be emailed to people (in pdf) and also brought to meetings.

We have a new logo and this design should be an extenstion of it from a colour, look and feel perspective. The piece should also be clean and not too copy heavy so we encourage use of sub-heads, whitespace, etc.

When we send this piece out or hand it to someone, the impression should be "I am comfortable with Dunfield Inc. they can help me and are people who get me, people I can trust to work closely with me on my business who are personally vested in my success".

Hello all, thank you for sumitting designs, there is some great work here.  A few changes/requests ...

Pls add the following headline on the front page right off the top

Entrepreneurs helping entrepreneurs, providing strategic financial services

Can we put Services on the front page? and call them out with treatment in a text box or with something strong that creates emphasis

Can the quote pls be broken up as opposed to one long list of 6 quotes? They can be floated throughout the piece, we can use less of them (or not) and put them on the front and back of the brochure? 

Also looking for the final product to be a little more bold in colour ...

Thx all, let us know if you have questions

Target Market(s)

Individuals (CEO) who runs their own established, yet growing business, who needs a business-minded CFO

Industry/Entity Type

Financial

Requirements
Must have
• Must have photo of founder, include his name and credentials under photo
All copy provide must be included
If not sure of a headline put in dummy text and we will provide headline or sub head copy
Should not have
• Fonts to be clean, no serif fonts. Should compliment logo, not the same font exactly but easily replicable in Microsoft Word and complimentary
No illustrations or cliche clip art

```html
<!DOCTYPE html>
<html lang="en">
<head>
<meta charset="utf-8">
<title>Dunfield Inc – Brochure</title>
<link href="https://fonts.googleapis.com/css2?family=Roboto:ital,wght@0,300;0,400;0,700;1,400&display=swap" rel="stylesheet">
<style>
  :root{
    --stage:#262626;
    --paper:#ffffff;
    --blue:#0a78c8;
    --tab-blue:#1a5fb4;
    --navy:#1f2a6b;
    --cyan:#2fbfde;
    --cyan-line:#5fd0ea;
    --panel:#e9e9ec;
    --ink:#3a3a3a;
    --headline:#2b2f6e;
  }
  *{box-sizing:border-box;margin:0;padding:0}
  html,body{width:1200px;height:835px;overflow:hidden;background:var(--stage)}
  body{position:relative;font-family:"Roboto",Arial,sans-serif;color:var(--ink)}
  .page{position:absolute;top:70px;width:541px;height:698px;background:var(--paper);overflow:hidden}
  .page--front{left:49px}
  .page--back{left:612px}
  .page-frame{position:absolute;left:0;top:0}
  .abs{position:absolute}

  /* header */
  .brand{left:70px;top:32px;display:flex;align-items:center;gap:8px}
  .brand-mark{width:22px;height:22px;background:var(--navy)}
  .brand-name{font-size:22px;font-weight:400;color:var(--navy);letter-spacing:.3px}
  .contact{top:30px;font-size:9.6px;line-height:14.6px;color:#fff;font-weight:300}
  .contact--address{left:301px}
  .contact--lines{left:414px}

  .headline{left:39px;top:119px;font-size:38px;font-weight:300;line-height:45px;color:var(--headline)}
  .subhead{left:40px;top:212px;font-size:24.5px;font-weight:700;color:var(--headline);white-space:nowrap}
  .intro{left:41px;top:266px;width:448px;font-size:9.2px;line-height:14.2px}

  .tab{position:absolute;height:21px;width:121px;background:var(--tab-blue);color:#fff;font-size:13px;line-height:21px;padding-left:7px}
  .tab::after{content:"";position:absolute;right:0;top:0;width:13px;height:100%;background:var(--navy);clip-path:polygon(100% 0,100% 100%,0 0)}

  .body-copy{font-size:8.3px;line-height:13.2px}
  .about{left:43px;top:363px;width:310px}
  .about p+p{margin-top:13px}

  .photo{left:370px;top:326px;width:113px;height:145px;background:linear-gradient(160deg,#4a4a4a,#1e1e22 60%,#2c2c34)}
  .caption{left:370px;top:474px;font-size:8.4px;line-height:12px}
  .caption small{display:block;font-size:6.4px}

  .services{left:31px;top:513px;width:479px;height:126px;background:var(--cyan)}
  .services .tab{left:12px;top:-9px}
  .service-list{position:absolute;top:33px;list-style:none;color:#fff;font-size:9.2px;line-height:12.3px}
  .service-list li{position:relative;padding-left:13px;margin-bottom:7.5px}
  .service-list li::before{content:"";position:absolute;left:0;top:2px;width:7px;height:7px;background:var(--tab-blue)}
  .service-list--a{left:16px;width:232px}
  .service-list--b{left:254px;width:214px}

  .url{top:665px;font-size:18px;color:var(--navy);font-weight:400}
  .page--front .url,.page--back .url{left:314px}

  /* back */
  .hero{left:44px;top:55px;width:255px;height:155px;background:linear-gradient(120deg,#0d1f3a,#1c4a7a 55%,#0a2a55)}
  .credentials{left:47px;top:217px;width:258px}
  .credentials p+p{margin-top:13px}

  .values{left:332px;top:71px;width:175px;height:396px;background:var(--panel)}
  .values .tab{left:14px;top:-10px;width:136px;height:22px;line-height:22px;font-size:13.5px;background:var(--blue)}
  .value-list{list-style:none;position:absolute;left:14px;top:35px;width:150px;font-size:9.2px;line-height:12.3px;color:#222}
  .value-list li{position:relative;padding-left:15px;margin-bottom:10px}
  .value-list li::before{content:"";position:absolute;left:0;top:3px;width:6px;height:6px;background:var(--blue)}

  .testimonials{left:31px;top:510px;width:477px;height:114px;background:var(--cyan)}
  .testimonials .tab{left:11px;top:-12px;height:22px;line-height:22px;font-size:13.5px}
  .quote{position:absolute;font-size:7.6px;line-height:12.3px;font-style:italic;color:#fff;font-weight:300}
  .quote--1{left:23px;top:22px;width:130px}
  .quote--2{left:183px;top:14px;width:125px}
  .quote--3{left:312px;top:14px;width:150px;border-left:1px solid var(--cyan-line);padding-left:6px}
  .quote--4{left:183px;top:76px;width:285px}
  .quote--2::before{content:"";position:absolute;left:-6px;top:0;height:50px;border-left:1px solid var(--cyan-line)}
  .fave{display:inline-block;float:right}
</style>
</head>
<body>

<section class="page page--front">
  <svg class="page-frame" width="541" height="698" viewBox="0 0 541 698" aria-hidden="true">
    <rect x="0" y="0" width="541" height="86" fill="var(--blue)"/>
    <rect x="0" y="84" width="541" height="5" fill="var(--cyan)"/>
    <rect x="0" y="89" width="541" height="4" fill="#fff"/>
    <path d="M43,93 L43,24 Q43,9 58,9 L247,9 Q262,9 264,26 L268,70 Q270,86 287,86 L290,93 Z" fill="#fff"/>
    <path d="M0,657 L280,657 Q296,657 300,672 L304,686 Q308,698 325,698 L0,698 Z" fill="var(--blue)"/>
    <path d="M505,698 Q522,698 527,684 L531,668 Q534,657 541,657 L541,698 Z" fill="var(--blue)"/>
    <path d="M290,657 Q298,660 300,672" stroke="var(--cyan)" stroke-width="3" fill="none"/>
    <path d="M531,668 Q534,660 541,659" stroke="var(--cyan)" stroke-width="3" fill="none"/>
  </svg>

  <div class="abs brand"><span class="brand-mark"></span><span class="brand-name">Dunfield Inc</span></div>
  <div class="abs contact contact--address">1820 Ridge Avenue SW,<br>Calgary Alberta,<br>Canada, T2R 1K6</div>
  <div class="abs contact contact--lines">P&nbsp; 403.555.0142<br>F 000 000 000<br>E martinh@dunfieldinc.ca</div>

  <h1 class="abs headline">Entrepreneurs helping<br>entrepreneurs,</h1>
  <h2 class="abs subhead">providing strategic financial services</h2>
  <p class="abs intro">By engaging Dunfield Inc, entrepreneurs can regularly access senior executive financial acumen and strategic discipline without having to hire a full-time financial executive or overspend on third-party service providers who are transactional in nature.</p>

  <div class="tab" style="left:43px;top:329px">Who we are?</div>
  <div class="abs about body-copy">
    <p>Dunfield Inc. evolved out of the companies, partnerships and relationships that Martin Halvorsen, its founder, has nurtured and built over the last 22 years. Mr. Halvorsen, the founder of Dunfield, is an entrepreneur himself having built his own companies and managed several successful investment funds whose mandates were to invest in entrepreneurial growth companies.</p>
    <p>Over his career, he has worked extensively with entrepreneurs like himself who have struggled to build an experienced and engaged executive management team.</p>
  </div>

  <div class="abs photo" role="img" aria-label="Portrait photo of the founder, Martin Halvorsen"></div>
  <div class="abs caption">Martin Halvorsen,<small>Founder</small></div>

  <div class="abs services">
    <div class="tab">Services</div>
    <ul class="service-list service-list--a">
      <li>We work intimately with our clients to determine their corporate and personal objectives</li>
      <li>We evaluate corporate strategies and assist in aligning them with financial ones</li>
      <li>We assist in budgeting, investing, financial forecasting and analysis and asset management</li>
    </ul>
    <ul class="service-list service-list--b">
      <li>We develop and implement accountability financial systems, processes and reporting</li>
      <li>We manage capital raising efforts, tax structuring issues and corporate transactions including mergers, acquisitions, and the sale of your business</li>
    </ul>
  </div>

  <div class="abs url">www.dunfieldinc.ca</div>
</section>

<section class="page page--back">
  <svg class="page-frame" width="541" height="698" viewBox="0 0 541 698" aria-hidden="true">
    <path d="M0,657 L280,657 Q296,657 300,672 L304,686 Q308,698 325,698 L0,698 Z" fill="var(--blue)"/>
    <path d="M505,698 Q522,698 527,684 L531,668 Q534,657 541,657 L541,698 Z" fill="var(--blue)"/>
    <path d="M290,657 Q298,660 300,672" stroke="var(--cyan)" stroke-width="3" fill="none"/>
    <path d="M531,668 Q534,660 541,659" stroke="var(--cyan)" stroke-width="3" fill="none"/>
  </svg>

  <div class="abs hero" role="img" aria-label="Photo of a businessman in a suit writing business keywords on a glass board"></div>
  <div class="abs credentials body-copy">
    <p>Mr. Halvorsen has a proven track record of developing and implementing strategic corporate policy. His experience and education is in corporate finance, portfolio management and building businesses and he is a registered Portfolio Manager. He also has earned an MBA from the University of Westbrook (1995) and is a Chartered Financial Analyst (CFA, 1999).</p>
    <p>He applies this competence to evaluating an entrepreneur’s vision and corporate strategies and assisting in translating them into higher growth, improved efficiency and higher profitability. He has extensive experience in public and private, debt and equity capital markets, involving raising, managing and investing capital and completing corporate transactions. He has evaluated hundreds of corporate business strategies for potential investment.</p>
    <p>Other core skills include financial and tax analysis, working with high-performing investment teams, managing financial and accounting functions, designing and implementing operational and compliance systems.</p>
  </div>

  <aside class="abs values">
    <div class="tab">Core Values</div>
    <ul class="value-list">
      <li>We love working with entrepreneurs because they like adventure. We understand the high energy, creativity and passion required to take high risks and achieve a corporate vision.</li>
      <li>We like entrepreneurs because they are focused on achievement. They are “can-do” people who take action.</li>
      <li>We like entrepreneurs because their business relationships are like family. Entrepreneurs are personally invested and value personal relationships with amazing people.</li>
      <li>We like entrepreneurs because they work hard and live well. Health and wellness is as important as financial success, and most of all having fun is central to the mind set of most successful entrepreneurs.</li>
    </ul>
  </aside>

  <div class="abs testimonials">
    <div class="tab">Testimonials</div>
    <p class="quote quote--1">“I need a financial executive who gets the numbers, can think strategically and translate that combined expertise and understanding into forward-looking corporate strategies” powerful</p>
    <p class="quote quote--2">“I need a financial executive who understands the inherent makeup of an entrepreneur”</p>
    <p class="quote quote--3">“If I could hire my equal in a financial capacity, my executive team would be complete” <span class="fave">martin’s fave</span></p>
    <p class="quote quote--4">“I need help implementing better financial systems and process that can be maintained in a disciplined way”</p>
  </div>

  <div class="abs url">www.dunfieldinc.ca</div>
</section>

</body>
</html>
```